Property management company looking for modern card design

We at Blue Heron Partners provides property management services for its residential and commercial properties, with expertise in all categories of multifamily, industrial and office projects throughout California.

We need a business card design that is professional and modern designed business card. In our field, clients get hundreds of business cards, we would like our card to stand out.

Please avoid small print.

Target Market(s)

Professionals and high end clients

Industry/Entity Type

Financial Planning

Contact Information for Business Card

Company Name: Blue Heron Partners, Name, email, license #, phone number, website blueheronpartners.com

Font styles to use
Sans Serif

Requirements
Must have
• The card design needs to be adaptable because there is a possibly we will be expanding into different sectors other than real estate. The card design should be focused on financial planning and asset management.
Nice to have
• Modern and simple business card. Eye catching. Non-standard size/shaped cards would be great.
• blueheronpartners.com
Should not have
• Too many bright color or any pictures or shapes of real estate stuff.

```html
<!DOCTYPE html>
<html lang="en">
<head>
<meta charset="UTF-8">
<title>Blue Heron Partners — Business Card</title>
<link href="https://fonts.googleapis.com/css2?family=Lato:wght@400;700&display=swap" rel="stylesheet">
<style>
  :root {
    --backdrop: #8d8178;
    --card-stock: #e4dac7;
    --card-edge: #d3c8b3;
    --brand-red: #e0202e;
    --mark-red: #b3131f;
    --ink: #1d1d1d;
    --ink-muted: #55534f;
    --rule: #2a2a2a;
  }
  * { box-sizing: border-box; margin: 0; padding: 0; }
  html, body {
    width: 1200px;
    height: 864px;
    overflow: hidden;
  }
  body {
    background: var(--backdrop);
    display: flex;
    align-items: center;
    justify-content: center;
    font-family: "Lato", sans-serif;
  }
  .business-card {
    position: relative;
    width: 840px;
    height: 480px;
    background: var(--card-stock);
    border: 1px solid var(--card-edge);
    box-shadow: 0 18px 40px rgba(0, 0, 0, 0.25);
  }
  .brand-block {
    position: absolute;
    left: 70px;
    top: 70px;
    width: 500px;
    text-align: center;
  }
  .brand-mark {
    display: block;
    width: 124px;
    height: 124px;
    margin: 0 auto 20px auto;
    border-radius: 50%;
    background: var(--mark-red);
  }
  .brand-name {
    font-size: 38px;
    font-weight: 700;
    letter-spacing: 0.14em;
    text-transform: uppercase;
    color: var(--brand-red);
    line-height: 1.1;
  }
  .brand-website {
    margin-top: 12px;
    font-size: 22px;
    font-weight: 700;
    color: var(--ink-muted);
    letter-spacing: 0.02em;
  }
  .contact-block {
    position: absolute;
    left: 470px;
    top: 300px;
    padding-left: 34px;
    border-left: 2px solid var(--rule);
    height: 120px;
    display: flex;
    flex-direction: column;
    justify-content: center;
    gap: 8px;
  }
  .contact-line {
    display: flex;
    align-items: center;
    gap: 12px;
    font-size: 24px;
    color: var(--ink);
  }
  .contact-icon {
    width: 22px;
    height: 22px;
    flex: none;
  }
  .license-line {
    font-size: 22px;
    font-weight: 700;
    color: var(--ink);
    margin-top: 4px;
  }
</style>
</head>
<body>
  <div class="business-card">
    <div class="brand-block">
      <span class="brand-mark"></span>
      <div class="brand-name">Blue Heron Partners</div>
      <div class="brand-website">www.blueheronpartners.com</div>
    </div>

    <div class="contact-block">
      <div class="contact-line">
        <svg class="contact-icon" viewBox="0 0 22 22" aria-hidden="true">
          <rect width="22" height="22" rx="3" fill="var(--brand-red)"/>
          <path d="M7 5c1 0 1.6 2.4 1.6 3 0 .7-1 1-1 1.6.5 1.6 1.9 3 3.5 3.6.6 0 .9-1 1.6-1 .6 0 3 .6 3 1.6 0 1.4-1.3 2.2-2.6 2.2C8.8 16 6 13.2 5 9.4 4.8 7 5.6 5 7 5z" fill="var(--ink)"/>
        </svg>
        <span>555-014-2870</span>
      </div>
      <div class="contact-line">
        <svg class="contact-icon" viewBox="0 0 22 22" aria-hidden="true">
          <rect width="22" height="22" rx="3" fill="var(--brand-red)"/>
          <rect x="4.5" y="6.5" width="13" height="9" fill="none" stroke="var(--ink)" stroke-width="1.6"/>
          <path d="M4.5 6.5l6.5 5 6.5-5" fill="none" stroke="var(--ink)" stroke-width="1.6"/>
        </svg>
        <span>info@blueheron.com</span>
      </div>
      <div class="license-line">Lic : 40581376</div>
    </div>
  </div>
</body>
</html>
```